New Business Card Design Project

I need a design for business cards, i am an electrical business called "Corvane Electrical and Communications" i need the cards to be double sided with the company logo on the back (attached) the front needs to say my company name, web site, email address, telephone number, and ABN number and electrical license number. I am open to different arrangements of the information but would like the background to be incorporating something electrical or something that looks smart. open to all additional ideas also.

The company colours are orange and grey see logo attached.

Business Name: Corvane Electrical and Communications
Website: corvaneelectricalandcomms.example.com.au
Email: brent@corvaneelectricalandcomms.example.com.au
Telephone(mobile): 0481209736
ABN: 71208349162
Lic No: 418273D

Target Market(s)

Business entities, Project Managers, Accounts, Clients

Industry/Entity Type

Electrician

Contact Information for Business Card

I need a design for business cards, i am an electrical business called "Corvane Electrical and Communications" i need the cards to be double sided with the company logo on the back (attached) the front needs to say my company name

Font styles to use
Serif
Sans Serif

Colors
f37122
5c5c5c

Requirements
Must have
• Must have the Logo on the back open to different ways of it being on the back but had in mind to keep it central but again open to other options
Nice to have
• A real modern cool background that is eye catching yet contemporary
Should not have
• No backgrounds of a light bulb or plug or anything like that

```html
<!DOCTYPE html>
<html lang="en">
<head>
<meta charset="utf-8">
<title>Corvane Electrical and Communications – Business Cards</title>
<link href="https://fonts.googleapis.com/css2?family=Open+Sans:wght@400;600;700&display=swap" rel="stylesheet">
<style>
  :root {
    --page: #2b2b2b;
    --card: #050505;
    --orange: #f7a823;
    --white: #ffffff;
    --muted: #d9d9d9;
    --ink: #1a1a1a;
    --label-dark: #7a4f00;
  }
  * { box-sizing: border-box; margin: 0; padding: 0; }
  html, body {
    width: 1200px; height: 900px; overflow: hidden;
    background: var(--page);
    font-family: "Open Sans", Arial, sans-serif;
  }
  .canvas { position: relative; width: 1200px; height: 900px; }

  .card {
    position: absolute;
    width: 540px; height: 310px;
    background: var(--card);
    border-radius: 18px;
    overflow: hidden;
    box-shadow: 0 14px 30px rgba(0,0,0,.45);
  }
  .card--back  { left: 60px;  top: 120px; }
  .card--front { left: 600px; top: 470px; }

  /* bottom colour band */
  .band { position: absolute; left: 0; right: 0; bottom: 0; height: 40px; }
  .band__base { position: absolute; left: 0; right: 0; bottom: 0; height: 12px; background: var(--orange); }
  .band__row { position: absolute; left: 0; right: 0; bottom: 12px; height: 28px; display: flex; }
  .band__seg--orange { background: var(--orange); }
  .band__seg--white  { background: var(--white); }
  .band__seg--left  { width: 46%; }
  .band__seg--mid   { width: 28%; }
  .band__seg--right { flex: 1; display: flex; align-items: center; justify-content: flex-end; padding-right: 16px; }

  /* brand wordmark */
  .brand { position: absolute; display: flex; align-items: center; gap: 12px; }
  .brand__dot { width: 18px; height: 18px; border-radius: 50%; background: var(--orange); flex: none; }
  .brand__name { color: var(--white); font-weight: 600; line-height: 1.15; }
  .card--back .brand { left: 70px; top: 88px; }
  .card--back .brand__name { font-size: 30px; }
  .card--front .brand { left: 28px; top: 200px; }
  .card--front .brand__name { font-size: 19px; }

  .web-line {
    position: absolute; right: 18px; bottom: 46px;
    color: var(--white); font-size: 13px;
  }
  .web-line .accent { color: var(--orange); }

  /* front details */
  .person { position: absolute; right: 18px; top: 20px; text-align: right; }
  .person__name { color: var(--orange); font-size: 22px; font-weight: 400; letter-spacing: .5px; }
  .person__role { color: var(--white); font-size: 10px; font-weight: 600; letter-spacing: .5px; }
  .rule { position: absolute; left: 22px; top: 60px; width: 345px; height: 1px; background: var(--muted); }

  .contacts { position: absolute; right: 18px; top: 84px; text-align: right; color: var(--white); font-size: 12.5px; line-height: 1.5; }
  .contacts__abn { margin-bottom: 10px; }
  .contacts__abn .label { color: var(--orange); }
  .contacts__row { display: flex; justify-content: flex-end; align-items: center; gap: 8px; }
  .contacts__row svg { width: 12px; height: 12px; flex: none; }

  .licence { color: var(--ink); font-size: 12px; }
  .licence .label { color: var(--label-dark); }
</style>
</head>
<body>
<div class="canvas">

  <!-- Logo side -->
  <section class="card card--back">
    <div class="brand">
      <span class="brand__dot"></span>
      <span class="brand__name">Corvane Electrical<br>and Communications</span>
    </div>
    <p class="web-line">www.<span class="accent">corvaneelectricalandcomms</span>.example.com.au</p>
    <div class="band">
      <div class="band__row">
        <div class="band__seg--orange band__seg--left"></div>
        <div class="band__seg--white band__seg--mid"></div>
        <div class="band__seg--orange band__seg--right"></div>
      </div>
      <div class="band__base"></div>
    </div>
  </section>

  <!-- Details side -->
  <section class="card card--front">
    <div class="person">
      <h1 class="person__name">MARLON PETRIE</h1>
      <p class="person__role">DIRECTOR</p>
    </div>
    <div class="rule"></div>

    <div class="contacts">
      <p class="contacts__abn"><span class="label">ABN:</span> 71208349162</p>
      <p class="contacts__row">0481-209-736
        <svg viewBox="0 0 24 24"><path fill="#f7a823" d="M6.6 10.8a15 15 0 0 0 6.6 6.6l2.2-2.2c.3-.3.7-.4 1-.2 1.1.4 2.3.6 3.6.6.6 0 1 .4 1 1V20c0 .6-.4 1-1 1A17 17 0 0 1 3 4c0-.6.4-1 1-1h3.5c.6 0 1 .4 1 1 0 1.3.2 2.5.6 3.6.1.3 0 .7-.2 1z"/></svg>
      </p>
      <p class="contacts__row">brent@corvaneelectricalandcomms.example.com.au
        <svg viewBox="0 0 24 24"><rect x="2" y="5" width="20" height="14" rx="2" fill="none" stroke="#f7a823" stroke-width="2.2"/><path d="M3 6l9 7 9-7" fill="none" stroke="#f7a823" stroke-width="2.2"/></svg>
      </p>
      <p class="contacts__row">www.corvaneelectricalandcomms.example.com.au
        <svg viewBox="0 0 24 24"><circle cx="12" cy="12" r="9.5" fill="none" stroke="#f7a823" stroke-width="2"/><ellipse cx="12" cy="12" rx="4" ry="9.5" fill="none" stroke="#f7a823" stroke-width="1.6"/><path d="M2.5 12h19M4 7h16M4 17h16" stroke="#f7a823" stroke-width="1.4"/></svg>
      </p>
    </div>

    <div class="brand">
      <span class="brand__dot"></span>
      <span class="brand__name">Corvane Electrical<br>and Communications</span>
    </div>

    <div class="band">
      <div class="band__row">
        <div class="band__seg--orange band__seg--left"></div>
        <div class="band__seg--white band__seg--mid"></div>
        <div class="band__seg--orange band__seg--right">
          <p class="licence"><span class="label">Lic No:</span> 418273D</p>
        </div>
      </div>
      <div class="band__base"></div>
    </div>
  </section>

</div>
</body>
</html>
```